Accountability Project Graphics

I want to create 10 social media graphics (new Instagram size 4:5 (1080 x 1350 pixels) focusing on our Quilvo Accountability App, using any of the 3 pictures attached. Use the attached pics only, NO RANDOM STOCK PHOTOGRAPHY. For the color scheme, use the landing page colors/fonts (attached).
You can add any of the 3 photos attached but I mainly need BOLD text that includes these headlines and sub-headlines on them.
Please NOTE for all the headlines below, also add this sub-headline on each graphic:
Stay Consistent with RT in Your Pocket!
Here are the headlines:
• Stop Starting Over Every Monday
• You don't need more willpower. You need more support
• Built for women who are tired of doing this alone
• When Motivation Fades, RT Checks In
• The Support System You've Been Missing
• Support When Motivation Disappears
• What if RT Checked in Every Day?
• The Missing Piece Isn't Another Diet
• Eat the food you love. Stay accountable every day.
• One Bad Meal Doesn't Mean You Failed
women over 40 trying to lose weight

```html
<!DOCTYPE html>
<html lang="en">
<head>
<meta charset="utf-8">
<title>Accountability Project Graphics</title>
<link rel="stylesheet" href="https://fonts.googleapis.com/css2?family=Playfair+Display:wght@700;800&family=Poppins:ital,wght@1,400;1,500&display=swap">
<style>
  :root {
    --bg: #ffffff;
    --rose: #cd5b83;
    --plum: #4a2f50;
    --ink: #ffffff;
    --photo-solo-a: #3a2e2e;
    --photo-solo-b: #1d2233;
    --photo-duo-a: #e9dccb;
    --photo-duo-b: #3e4d6e;
    --photo-hug-a: #e7b3b8;
    --photo-hug-b: #e2386f;
  }
  * { box-sizing: border-box; margin: 0; padding: 0; }
  html, body { width: 1200px; height: 2785px; overflow: hidden; background: var(--bg); }
  .canvas { position: relative; width: 1200px; height: 2785px; }
  .post {
    position: absolute; width: 374px; height: 468px;
    display: flex; overflow: hidden;
  }
  .col-a { left: 224px; }
  .col-b { left: 609px; }
  .row-1 { top: 199px; } .row-2 { top: 679px; } .row-3 { top: 1157px; }
  .row-4 { top: 1636px; } .row-5 { top: 2116px; }
  .panel {
    position: relative; z-index: 1;
    flex: none; height: 100%; color: var(--ink);
    padding: var(--top, 60px) 0 0 var(--left, 13px);
    display: flex; flex-direction: column;
  }
  .panel--rose { background: var(--rose); }
  .panel--plum { background: var(--plum); }
  .headline {
    font-family: "Playfair Display", Georgia, serif; font-weight: 700;
    font-size: var(--size, 40px); line-height: var(--lh, 1.2);
    white-space: nowrap;
  }
  .headline-small { font-size: 29px; }
  .divider { flex: none; width: 69px; height: 1.5px; background: var(--ink); margin: 14px 0 14px; }
  .sub {
    font-family: "Poppins", Arial, sans-serif; font-style: italic; font-weight: 400;
    font-size: 15px; line-height: 1.45; letter-spacing: 0.5px; white-space: nowrap;
  }
  .photo { flex: 1; height: 100%; }
  .photo--solo { background: linear-gradient(160deg, var(--photo-solo-a) 0%, var(--photo-solo-b) 60%, #c8c8cc 100%); }
  .photo--duo { background: linear-gradient(180deg, var(--photo-duo-a) 0%, var(--photo-duo-a) 40%, var(--photo-duo-b) 100%); }
  .photo--hug { background: linear-gradient(160deg, var(--photo-hug-a) 0%, #d7c3b5 45%, var(--photo-hug-b) 100%); }
</style>
</head>
<body>
<main class="canvas">

  <section class="post col-a row-1">
    <div class="panel panel--rose" style="width:203px;--top:62px;--size:48px;--lh:1.06">
      <h2 class="headline">Stop<br>Starting<br>Over<br>Every<br>Monday</h2>
      <span class="divider"></span>
      <p class="sub">Stay Consistent with<br>RT in Your Pocket!</p>
    </div>
    <div class="photo photo--solo" role="img" aria-label="Smiling coach in a black outfit, hand on hip"></div>
  </section>

  <section class="post col-b row-1">
    <div class="photo photo--duo" role="img" aria-label="Two women laughing together"></div>
    <div class="panel panel--plum" style="width:215px;--top:28px;--left:18px;--size:35px;--lh:1.37">
      <h2 class="headline">You Don't<br>Need<br>More<br>Willpower.<br>You Need<br>More<br>Support</h2>
      <span class="divider"></span>
      <p class="sub">Stay Consistent with<br>RT in Your Pocket!</p>
    </div>
  </section>

  <section class="post col-a row-2">
    <div class="panel panel--plum" style="width:189px;--top:20px;--left:9px;--size:40px;--lh:1.25">
      <h2 class="headline">Built For<br>Women<br>Who Are<br>Tired Of<br>Doing<br>This<br>Alone</h2>
      <span class="divider"></span>
      <p class="sub">Stay Consistent with<br>RT in Your Pocket!</p>
    </div>
    <div class="photo photo--hug" role="img" aria-label="Coach hugging a woman and laughing"></div>
  </section>

  <section class="post col-b row-2">
    <div class="panel panel--rose" style="width:205px;--top:76px;--size:40px;--lh:1.2">
      <h2 class="headline">One Bad<br>Meal<br>Doesn't<br>Mean<br>You Failed</h2>
      <span class="divider"></span>
      <p class="sub">Stay Consistent with<br>RT in Your Pocket!</p>
    </div>
    <div class="photo photo--solo" role="img" aria-label="Smiling coach in a black outfit, hand on hip"></div>
  </section>

  <section class="post col-a row-3">
    <div class="photo photo--duo" role="img" aria-label="Two women laughing together"></div>
    <div class="panel panel--plum" style="width:215px;--top:46px;--left:18px;--size:40px;--lh:1.2">
      <h2 class="headline">The<br>Support<br>System<br>You've<br>Been<br>Missing</h2>
      <span class="divider"></span>
      <p class="sub">Stay Consistent with<br>RT in Your Pocket!</p>
    </div>
  </section>

  <section class="post col-b row-3">
    <div class="panel panel--rose" style="width:191px;--top:96px;--left:9px;--size:32px;--lh:1.2">
      <h2 class="headline">Support<br>When<br>Motivation<br>Disappears</h2>
      <span class="divider"></span>
      <p class="sub">Stay Consistent with<br>RT in Your Pocket!</p>
    </div>
    <div class="photo photo--hug" role="img" aria-label="Coach hugging a woman and laughing"></div>
  </section>

  <section class="post col-a row-4">
    <div class="panel panel--rose" style="width:203px;--top:62px;--size:48px;--lh:1.09">
      <h2 class="headline">What<br>If RT<br>Checked<br>In Every<br>Day?</h2>
      <span class="divider"></span>
      <p class="sub">Stay Consistent with<br>RT in Your Pocket!</p>
    </div>
    <div class="photo photo--solo" role="img" aria-label="Smiling coach in a black outfit, hand on hip"></div>
  </section>

  <section class="post col-b row-4">
    <div class="photo photo--duo" role="img" aria-label="Two women laughing together"></div>
    <div class="panel panel--plum" style="width:215px;--top:48px;--left:22px;--size:41px;--lh:1.19">
      <h2 class="headline">The<br>Missing<br>Piece<br>Isn't<br>Another<br>Diet</h2>
      <span class="divider"></span>
      <p class="sub">Stay Consistent with<br>RT in Your Pocket!</p>
    </div>
  </section>

  <section class="post col-a row-5">
    <div class="panel panel--plum" style="width:189px;--top:42px;--left:9px;--size:38px;--lh:1.14">
      <h2 class="headline">Eat The<br>Food You<br>Love.<br>Stay<br><span class="headline-small">Accountable</span><br>Every<br>Day.</h2>
      <span class="divider"></span>
      <p class="sub">Stay Consistent with<br>RT in Your Pocket!</p>
    </div>
    <div class="photo photo--hug" role="img" aria-label="Coach hugging a woman and laughing"></div>
  </section>

  <section class="post col-b row-5">
    <div class="panel panel--rose" style="width:205px;--top:96px;--size:36px;--lh:1.25">
      <h2 class="headline">When<br>Motivation<br>Fades, RT<br>Checks In</h2>
      <span class="divider"></span>
      <p class="sub">Stay Consistent with<br>RT in Your Pocket!</p>
    </div>
    <div class="photo photo--solo" role="img" aria-label="Smiling coach in a black outfit, hand on hip"></div>
  </section>

</main>
</body>
</html>
```